A clean crisp business card for a Landscape Construction company. Designed to be easy to read contact/ info and also be appealing/interesting, unlike a traditional business card.

Industry/Entity Type

Landscape Construction

Contact Information for Business Card

Company name : Brambleford Landscape Construction, phone number: (877) 62Vista, website:Bramblefordyards.example, Email, sales@bramblefordyards.example

Requirements
Nice to have
• Luxurious finishes/ details…. Icons or emblems next to contact info
Should not have
• Clipart or general pictures

```html
<!DOCTYPE html>
<html lang="en">
<head>
<meta charset="utf-8">
<title>Brambleford Landscape Construction – Business Card</title>
<link href="https://fonts.googleapis.com/css2?family=Roboto:wght@400;500;700&display=swap" rel="stylesheet">
<style>
  :root {
    --backdrop: #1f2022;
    --brand-blue: #2a74c4;
    --brand-blue-deep: #1d5fae;
    --brand-blue-light: #3a86d2;
    --leaf-green: #8cc63f;
    --paper: #ffffff;
    --ink-light: #ffffff;
  }
  * { box-sizing: border-box; margin: 0; padding: 0; }
  html, body {
    width: 1200px; height: 900px; overflow: hidden;
    background: var(--backdrop);
    font-family: "Roboto", Arial, sans-serif;
  }
  .canvas {
    position: relative; width: 1200px; height: 900px;
    display: flex; justify-content: center; align-items: center; gap: 90px;
  }
  .card {
    position: relative; width: 340px; height: 590px;
    border-radius: 16px; overflow: hidden;
    background: linear-gradient(160deg, var(--brand-blue-light), var(--brand-blue) 55%, var(--brand-blue-deep));
  }

  /* Brand side */
  .card--brand { display: flex; align-items: center; justify-content: center; }
  .wordmark {
    text-align: center; font-weight: 500; color: var(--ink-light);
    text-transform: uppercase;
  }
  .wordmark__name { display: block; font-size: 36px; letter-spacing: 2px; line-height: 1.15; }
  .wordmark__tag { display: block; font-size: 13px; letter-spacing: 4.2px; margin-top: 6px; }

  /* Contact side */
  .card--contact { color: var(--ink-light); }
  .contact {
    position: absolute; top: 40px; left: 0; right: 0;
    text-align: center; padding: 0 28px;
  }
  .contact__name {
    font-size: 30px; font-weight: 700; color: var(--leaf-green);
    letter-spacing: 1px; text-transform: uppercase;
  }
  .contact__role { font-size: 15px; margin-top: 2px; }
  .contact__rule { height: 1px; background: var(--leaf-green); margin: 14px 20px; }
  .contact__icons { display: flex; justify-content: center; gap: 6px; margin-bottom: 10px; }
  .contact__icon {
    width: 18px; height: 18px; border-radius: 3px; background: var(--leaf-green);
    display: flex; align-items: center; justify-content: center;
  }
  .contact__line { font-size: 15px; line-height: 22px; }
  .wave { position: absolute; left: 0; bottom: 0; width: 340px; height: 290px; }
  .card--contact .wordmark {
    position: absolute; left: 22px; bottom: 34px; text-align: left; color: var(--brand-blue);
  }
  .card--contact .wordmark__name { font-size: 30px; }
  .card--contact .wordmark__tag { font-size: 11px; letter-spacing: 3.4px; color: var(--leaf-green); }
</style>
</head>
<body>
<main class="canvas">

  <section class="card card--brand" aria-label="Card back">
    <div class="wordmark">
      <span class="wordmark__name">Brambleford</span>
      <span class="wordmark__tag">Landscape Construction</span>
    </div>
  </section>

  <section class="card card--contact" aria-label="Card front">
    <div class="contact">
      <h1 class="contact__name">Dana Whitlow</h1>
      <p class="contact__role">Founder</p>
      <div class="contact__rule"></div>
      <div class="contact__icons">
        <span class="contact__icon">
          <svg width="11" height="11" viewBox="0 0 24 24" aria-hidden="true"><path fill="#fff" d="M6.6 10.8a15 15 0 0 0 6.6 6.6l2.2-2.2c.3-.3.7-.4 1-.2 1.1.4 2.3.6 3.6.6.6 0 1 .4 1 1V20c0 .6-.4 1-1 1A17 17 0 0 1 3 4c0-.6.4-1 1-1h3.5c.6 0 1 .4 1 1 0 1.3.2 2.5.6 3.6.1.3 0 .7-.2 1z"/></svg>
        </span>
        <span class="contact__icon">
          <svg width="11" height="11" viewBox="0 0 24 24" aria-hidden="true"><path fill="#fff" d="M3 5h18v14H3z"/><path fill="none" stroke="#8cc63f" stroke-width="2" d="M3 6l9 7 9-7"/></svg>
        </span>
        <span class="contact__icon">
          <svg width="11" height="11" viewBox="0 0 24 24" aria-hidden="true"><circle cx="12" cy="12" r="9" fill="none" stroke="#fff" stroke-width="2"/><path fill="none" stroke="#fff" stroke-width="2" d="M3 12h18M12 3c3 3 3 15 0 18M12 3c-3 3-3 15 0 18"/></svg>
        </span>
      </div>
      <p class="contact__line">(877) 62Vista</p>
      <p class="contact__line">sales@bramblefordyards.example</p>
      <p class="contact__line">bramblefordyards.example</p>
      <div class="contact__rule"></div>
      <p class="contact__line">1420 Harlow Street</p>
      <p class="contact__line">Country Name, AB 48210</p>
    </div>

    <svg class="wave" viewBox="0 0 340 290" aria-hidden="true">
      <path fill="#ffffff" d="M0 12 C 80 22, 110 114, 200 144 S 320 164, 346 170 L 346 290 L 0 290 Z"/>
      <path fill="none" stroke="#8cc63f" stroke-width="6" d="M0 10 C 80 20, 110 112, 200 142 S 320 162, 346 168"/>
      <path fill="none" stroke="#1d5fae" stroke-width="3" d="M0 26 C 76 36, 104 128, 194 158 S 318 178, 346 184"/>
    </svg>

    <div class="wordmark">
      <span class="wordmark__name">Brambleford</span>
      <span class="wordmark__tag">Landscape Construction</span>
    </div>
  </section>

</main>
</body>
</html>
```